Professional & attention grabbing.

A business card design, front and back. I already have a logo I will attach, but I am open to something new as well.
Things to include:
Name:
Title:
Phone:
Email:
Wanting something that is professional but attention grabbing.
Also we do a lot of work using drones on natural gas pipelines (leading the future)if you want to include any of that. I'm open to ideas.
Target Market(s)
Natural gas transmission industry / greenhouse gas mitigation industry
Industry/Entity Type
Business
Colors
Designer to choose colors to be used in the design.
Look and feel
Each slider illustrates characteristics of the customer's brand and the style your logo design should communicate.

```html
<!DOCTYPE html>
<html lang="en">
<head>
<meta charset="utf-8">
<title>Kestrel Inspections – Business Card</title>
<link rel="stylesheet" href="https://fonts.googleapis.com/css2?family=Source+Sans+3:ital,wght@0,400;0,600;0,700;1,400&display=swap">
<style>
  :root {
    --page-bg: #e4e4e4;
    --card-white: #ffffff;
    --brand-red: #c01f25;
    --brand-dark: #3a3b3d;
    --text-dark: #3d3d3d;
    --text-light: #ffffff;
  }
  * { margin: 0; padding: 0; box-sizing: border-box; }
  html, body {
    width: 1200px; height: 987px; overflow: hidden;
    background: var(--page-bg);
    font-family: "Source Sans 3", "Helvetica Neue", Arial, sans-serif;
  }
  .canvas { position: relative; width: 1200px; height: 987px; }
  .card {
    position: absolute; left: 293px; width: 615px; height: 352px; overflow: hidden;
  }
  .card--front { top: 130px; background: var(--card-white); }
  .card--back { top: 505px; background: var(--brand-red); }

  .brand {
    position: absolute; left: 33px; top: 44px;
    display: flex; align-items: center; gap: 12px;
  }
  .brand__square { width: 44px; height: 44px; background: var(--brand-red); }
  .brand__name {
    font-weight: 700; font-size: 34px; line-height: 1; letter-spacing: 1px;
    color: var(--brand-dark);
  }

  .contact {
    position: absolute; right: 24px; top: 200px; text-align: right;
    color: var(--text-dark);
  }
  .contact__name {
    font-weight: 600; font-size: 22px; line-height: 1; color: var(--brand-red);
    letter-spacing: 0.3px;
  }
  .contact__title { font-size: 17px; line-height: 1; margin-top: 8px; }
  .contact__line {
    display: flex; justify-content: flex-end; align-items: center; gap: 8px;
    font-size: 16px; line-height: 1; margin-top: 13px;
  }
  .contact__line + .contact__line { margin-top: 8px; }
  .contact__title + .contact__line { margin-top: 16px; }
  .icon { width: 15px; height: 15px; fill: var(--brand-red); }

  .front-band { position: absolute; left: 0; bottom: 0; width: 615px; height: 36px; }
  .front-band__url {
    position: absolute; right: 27px; bottom: 8px;
    font-style: italic; font-size: 16px; letter-spacing: 2.4px; color: var(--text-light);
  }

  .back-brand {
    position: absolute; right: 52px; top: 208px;
    display: flex; align-items: center; gap: 12px;
  }
  .back-brand__square { width: 40px; height: 40px; background: var(--card-white); }
  .back-brand__name {
    font-weight: 700; font-size: 32px; line-height: 1; letter-spacing: 1px;
    color: var(--text-light);
  }
  .back-url {
    position: absolute; right: 38px; top: 313px;
    font-style: italic; font-size: 16px; color: var(--text-light);
  }
</style>
</head>
<body>
<main class="canvas">
  <section class="card card--front" aria-label="Card front">
    <div class="brand">
      <span class="brand__square"></span>
      <span class="brand__name">KESTREL</span>
    </div>

    <div class="contact">
      <p class="contact__name">DANIEL REYES</p>
      <p class="contact__title">CEO/FOUNDER</p>
      <p class="contact__line">555 210 4417
        <svg class="icon" viewBox="0 0 24 24" aria-hidden="true"><path d="M6.6 10.8a15.1 15.1 0 0 0 6.6 6.6l2.2-2.2a1 1 0 0 1 1-.25 11.4 11.4 0 0 0 3.6.57 1 1 0 0 1 1 1V20a1 1 0 0 1-1 1A17 17 0 0 1 3 4a1 1 0 0 1 1-1h3.5a1 1 0 0 1 1 1c0 1.25.2 2.45.57 3.6a1 1 0 0 1-.25 1z"/></svg>
      </p>
      <p class="contact__line">daniel@kestrelinspect.com
        <svg class="icon" viewBox="0 0 24 24" aria-hidden="true"><path d="M2 5h20v14H2z M3.5 6.5 12 13l8.5-6.5" fill="var(--brand-red)"/><path d="M3 6.5 12 13l9-6.5" fill="none" stroke="#fff" stroke-width="1.6"/></svg>
      </p>
    </div>

    <div class="front-band">
      <svg width="615" height="36" viewBox="0 0 615 36" aria-hidden="true">
        <rect x="0" y="12" width="400" height="7" fill="var(--brand-red)"/>
        <rect x="0" y="24" width="615" height="12" fill="var(--brand-dark)"/>
        <polygon points="387,0 615,0 615,36 371,36" fill="var(--brand-dark)"/>
      </svg>
      <span class="front-band__url">www.kestrelinspect.com</span>
    </div>
  </section>

  <section class="card card--back" aria-label="Card back">
    <div class="back-brand">
      <span class="back-brand__square"></span>
      <span class="back-brand__name">KESTREL</span>
    </div>
    <p class="back-url">www.kestrelinspect.com</p>
  </section>
</main>
</body>
</html>
```